Refresh Brightpath Coursecraft

Need a new design for e-learning development and web app development site: http://brightpathcoursecraft.example. Need pages for everything on menu bar plus a training services and a web app development services pages and a better page for samples http://brightpathcoursecraft.example/samples5/.

***Must be programmed in html 5. NO CMS. No WP. No Plume. Straight html/css.

Target Market(s)

government

Industry/Entity Type

Government

Coding

Coded - Design and coding required

Number of Pages Required

1 page

Requirements
Must have
• Must be coded in html5/css. No CMS.
• Divided so you can easily see that we offer 3 separate services:
• Live Training - E-Learning Development - Web App Development
• A way to display logos of all our clients like on bottom of this page: https://www.quorvatests.example (this is also our website so you can copy all these logos)
• List both our Denver location which is already on our website plus our office in Velmoro Plaza. Street 62 Sur, 14-87. Medellín, Antioquia.
• A page like this for our web app dev services https://www.tekvanu.example/product-development
Should not have
• CMS

```html
<!DOCTYPE html>
<html lang="en">
<head>
<meta charset="utf-8">
<title>Brightpath Coursecraft</title>
<link href="https://fonts.googleapis.com/css2?family=Lato:wght@400;700;900&display=swap" rel="stylesheet">
<style>
:root{
  --orange:#f6a133;
  --blue:#1e6fae;
  --blue-dark:#1b5e96;
  --grey:#4a4a4a;
  --ink:#1d2430;
  --text:#3a3a3a;
  --light:#eeeeee;
  --white:#ffffff;
}
*{margin:0;padding:0;box-sizing:border-box}
html,body{width:1200px;height:3922px;overflow:hidden}
body{font-family:'Lato',sans-serif;color:var(--text);background:var(--white);position:relative}
.abs{position:absolute}
.site-header{left:0;top:0;width:1200px;height:110px;display:flex;align-items:center;justify-content:space-between;padding:0 76px}
.brand{display:flex;align-items:center;gap:14px;font-weight:700;font-size:24px;color:var(--blue)}
.brand-dot{width:46px;height:46px;border-radius:50%;background:var(--orange)}
.main-nav{display:flex;gap:46px;font-size:15px;font-weight:700;color:var(--ink)}
.hero{left:0;top:110px;width:1200px;height:570px;background:linear-gradient(135deg,#d9d6d0 0%,#8d8a86 45%,#c7c2ba 100%)}
.hero-shade{position:absolute;inset:0;background:rgba(0,0,0,.25)}
.hero h1{position:absolute;left:0;width:1200px;top:196px;text-align:center;color:var(--white);font-weight:900;font-size:50px;line-height:58px}
.btn-solid{position:absolute;left:510px;top:334px;width:180px;height:48px;background:var(--orange);color:var(--white);font-weight:700;font-size:17px;display:flex;align-items:center;justify-content:center}
.intro{left:76px;top:730px;width:1048px;text-align:center}
.intro h2{font-size:30px;font-weight:700;color:var(--ink);margin-bottom:26px}
.intro p{font-size:17px;line-height:29px}
.btn-outline{display:flex;align-items:center;justify-content:center;border:2px solid #9aa4b0;color:var(--blue);font-size:16px;font-weight:700;width:180px;height:46px;border-radius:3px}
.intro .btn-outline{position:absolute;left:434px;top:242px}
.divider{left:76px;top:1103px;width:1048px;height:1px;background:#d5d5d5}
.section-title{left:0;width:1200px;text-align:center;font-size:30px;font-weight:700;color:var(--ink)}
.service{left:0;width:1200px}
.service h3{position:absolute;font-size:30px;font-weight:900;color:var(--white)}
.service p{position:absolute;width:510px;font-size:15px;line-height:29px;color:var(--white)}
.service .btn-outline{position:absolute;border-color:var(--white);color:var(--white);border-radius:2px}
.photo{position:absolute;width:512px;height:313px}
.svc-live{top:1229px;height:413px;background:var(--orange);clip-path:polygon(0 0,100% 0,100% 70%,0 100%)}
.svc-elearn{top:1686px;height:404px;background:var(--blue);clip-path:polygon(0 0,100% 0,100% 100%,0 72%)}
.svc-webapp{top:2149px;height:465px;background:var(--grey);clip-path:polygon(0 0,100% 0,100% 72%,0 100%)}
.clients{left:0;top:2614px;width:1200px;height:400px;background:var(--light)}
.clients h2{position:absolute;top:45px;width:1200px;text-align:center;font-size:20px;font-weight:900;color:var(--ink)}
.logo-grid{position:absolute;left:76px;top:99px;display:grid;grid-template-columns:repeat(6,163px);grid-auto-rows:105px;gap:14px 14px}
.logo-card{background:var(--white);border:1px solid #dcdcdc;display:flex;align-items:center;justify-content:center;gap:8px;font-size:16px;font-weight:700;color:var(--blue-dark);text-align:center;padding:0 8px}
.logo-card i{width:14px;height:14px;border-radius:50%;background:var(--blue-dark);flex:none}
.dots{position:absolute;top:355px;left:576px;display:flex;gap:8px}
.dots span{width:9px;height:9px;border-radius:50%;background:#b8b8b8}
.dots span:first-child{background:var(--blue)}
.location{width:512px;text-align:center}
.location h3{font-size:19px;font-weight:900;color:var(--blue);margin-bottom:12px}
.location p{font-size:16px;line-height:26px;color:var(--ink)}
.location svg{vertical-align:-2px;margin-right:6px}
.map{position:absolute;width:512px;height:306px;top:3254px;background:linear-gradient(120deg,#e7e3da 0%,#ece8df 60%,#bcd3ea 100%)}
.touch{left:0;top:3628px;width:1200px;height:128px;background:linear-gradient(90deg,var(--blue) 0%,#3c7ea6 45%,var(--orange) 100%)}
.touch h2{position:absolute;left:117px;top:46px;color:var(--white);font-size:30px;font-weight:700}
.field{position:absolute;top:41px;width:264px;height:44px;background:var(--white);font-size:14px;color:#666;padding:13px 12px}
.btn-subscribe{position:absolute;left:892px;top:41px;width:188px;height:44px;background:var(--blue-dark);color:var(--white);font-weight:700;font-size:16px;display:flex;align-items:center;justify-content:center}
.footer-nav{left:0;top:3795px;width:1200px;display:flex;justify-content:center;gap:42px;font-size:13px;font-weight:700;color:var(--ink)}
.copyright{left:0;top:3829px;width:1200px;text-align:center;font-size:12px;color:#555}
.social{left:0;top:3858px;width:1200px;display:flex;justify-content:center;gap:18px}
.social span{width:22px;height:22px;border-radius:50%;background:#8e98a6}
</style>
</head>
<body>

<header class="site-header abs">
  <div class="brand"><span class="brand-dot"></span>Brightpath Coursecraft</div>
  <nav class="main-nav"><span>HOME</span><span>PORTFOLIO</span><span>TEAM &amp; EXPERIENCE</span><span>CONTACTS</span></nav>
</header>

<section class="hero abs">
  <div class="hero-shade" role="img" aria-label="Photo of hands typing on a laptop showing an e-learning course"></div>
  <h1>WE CREATE ENGAGING TRAINING<br>THAT EXCEED EXPECTATIONS.</h1>
  <div class="btn-solid">GET STARTED</div>
</section>

<section class="intro abs">
  <h2>INSTRUCTIONAL DESIGN AND COURSEWARE DEVELOPMENT FIRM</h2>
  <p>Brightpath Coursecraft is a HUBZone Certified, SBA 8(a) Certified, Native American Owned Small Disadvantaged Business located in Denver, Colorado. We have designed and delivered SCORM compliant eLearning, webinar, web-based training (WBT), instructor-led training (ILT), virtual ILT (vILT), blended, and 3D Immersive training courses. The Instructional Design Team brings nearly one hundred years of Instructional Design experience. Our Instructional Designers have experience designing, developing, and delivering custom technical and business skill training courses.</p>
  <div class="btn-outline">READ MORE</div>
</section>

<div class="divider abs"></div>
<h2 class="section-title abs" style="top:1150px">WHAT WE OFFERS</h2>

<section class="service svc-live abs">
  <h3 style="left:76px;top:66px">LIVE TRAINING</h3>
  <p style="left:76px;top:117px">Lorem ipsum dolor sit amet, consectetur adipiscing elit. Vestibulum diam felis, scelerisque ut quam ut, auctor maximus tellus. Sed lectus ipsum, consectetur et consequat et, aliquet ac tellus. Nunc vulputate egestas imperdiet maximus ex, at dignissim magna porta eget...</p>
  <div class="btn-outline" style="left:76px;top:263px">READ MORE</div>
</section>
<div class="photo" style="left:614px;top:1281px;background:linear-gradient(135deg,#e9e6e0,#9b8d7c)" role="img" aria-label="Photo of a small team working together at a laptop"></div>

<section class="service svc-elearn abs">
  <h3 style="left:616px;top:60px">E-LEARNING DEVELOPMENT</h3>
  <p style="left:616px;top:110px">Lorem ipsum dolor sit amet, consectetur adipiscing elit. Vestibulum diam felis, scelerisque ut quam ut, auctor maximus tellus. Sed lectus ipsum, consectetur et consequat et, aliquet ac tellus. Nunc vulputate egestas imperdiet maximus ex, at dignissim magna porta eget...</p>
  <div class="btn-outline" style="left:614px;top:253px">READ MORE</div>
</section>
<div class="photo" style="left:76px;top:1733px;background:linear-gradient(135deg,#c9ccd0,#3a4048)" role="img" aria-label="Photo of developers reviewing code on monitors"></div>

<section class="service svc-webapp abs">
  <h3 style="left:78px;top:82px">WEB APP DEVELOPMENT</h3>
  <p style="left:76px;top:133px">Lorem ipsum dolor sit amet, consectetur adipiscing elit. Vestibulum diam felis, scelerisque ut quam ut, auctor maximus tellus. Sed lectus ipsum, consectetur et consequat et, aliquet ac tellus. Nunc vulputate egestas imperdiet maximus ex, at dignissim magna porta eget...</p>
  <div class="btn-outline" style="left:76px;top:277px">READ MORE</div>
</section>
<div class="photo" style="left:614px;top:2201px;background:linear-gradient(135deg,#f1efec,#b7b1aa)" role="img" aria-label="Photo of hands sketching app screen wireframes on paper"></div>

<section class="clients abs">
  <h2>A FEW OF OUR 75,000 CLIENTS</h2>
  <div class="logo-grid">
    <div class="logo-card"><i></i>Aerowing Corps</div>
    <div class="logo-card"><i></i>Stonebrook</div>
    <div class="logo-card"><i></i>Vernhill University</div>
    <div class="logo-card"><i></i>Biolattice</div>
    <div class="logo-card"><i></i>Calvera</div>
    <div class="logo-card"><i></i>Ridgeford College</div>
    <div class="logo-card"><i></i>Sunvale</div>
    <div class="logo-card"><i></i>Trailwork Corps</div>
    <div class="logo-card"><i></i>Prairie State</div>
    <div class="logo-card"><i></i>Ocren</div>
    <div class="logo-card"><i></i>Linden Institute</div>
    <div class="logo-card"><i></i>Arcway</div>
  </div>
  <div class="dots"><span></span><span></span><span></span></div>
</section>

<h2 class="section-title abs" style="top:3070px;font-size:34px">LOCATIONS</h2>

<div class="location abs" style="left:76px;top:3140px">
  <h3>AURORA LOCATION</h3>
  <p><svg width="11" height="15" viewBox="0 0 11 15"><path d="M5.5 0A5.5 5.5 0 0 0 0 5.5C0 9.6 5.5 15 5.5 15S11 9.6 11 5.5A5.5 5.5 0 0 0 5.5 0zm0 7.7a2.2 2.2 0 1 1 0-4.4 2.2 2.2 0 0 1 0 4.4z" fill="#1e6fae"/></svg>Velmoro Plaza. Street 62 Sur, 14-87. Medellín,<br>Antioquia.</p>
</div>
<div class="location abs" style="left:614px;top:3140px">
  <h3>DENVER LOCATION</h3>
  <p><svg width="11" height="15" viewBox="0 0 11 15"><path d="M5.5 0A5.5 5.5 0 0 0 0 5.5C0 9.6 5.5 15 5.5 15S11 9.6 11 5.5A5.5 5.5 0 0 0 5.5 0zm0 7.7a2.2 2.2 0 1 1 0-4.4 2.2 2.2 0 0 1 0 4.4z" fill="#1e6fae"/></svg>7730 E Larkspur Avenue, Suite 2-210 Aurora, CO. 80012<br><svg width="13" height="13" viewBox="0 0 13 13"><path d="M2.6 0.5l2 2.6-1.2 1.6c.8 1.8 2.2 3.2 4 4l1.6-1.2 2.6 2-1.2 2.3C6 11.6 1.4 7 .3 1.7z" fill="#1e6fae"/></svg>+1 555 014 7720</p>
</div>
<div class="map" style="left:76px" role="img" aria-label="Street map with a pin marking the Aurora office"></div>
<div class="map" style="left:614px" role="img" aria-label="Street map with a pin marking the Denver office"></div>

<section class="touch abs">
  <h2>GET IN TOUCH</h2>
  <div class="field" style="left:340px">Enter Name</div>
  <div class="field" style="left:612px">Email Address</div>
  <div class="btn-subscribe">SUBSCRIBE NOW</div>
</section>

<nav class="footer-nav abs"><span>HOME</span><span>PORTFOLIO</span><span>TEAM &amp; EXPERIENCE</span><span>CONTACTS</span></nav>
<p class="copyright abs">Copyright © 2019, Company Name. All Right reserved</p>
<div class="social abs" aria-label="Social links"><span></span><span></span><span></span><span></span><span></span></div>

</body>
</html>
```